Verodex business card

Business card for sustainable investment company called "Verodex". Verodex is an exchange platform selling carbon credits between buyers and sellers. Carbon Credits are an environmental commodity for reducing global carbon emissions.

the card should obviously have our logo and the theme should be sustainability/environment mixed with a trading platform.

Contact Information for Business Card

Logo, Name, Title, Phone, Email

Colors
0054AA
0677BA
7BADD7
CADEEF
E8F1F8
0094D4
00A9DD
6FCCEA
C7EBF8
E9F6FB
00AB8E
00BBA5
67D7C9
C6EFE9
E9F9F6
59FF00
82FF00
B8FF75
E3FFCB
F4FFEA

```html
<!DOCTYPE html>
<html lang="en">
<head>
<meta charset="utf-8">
<title>Verodex business card</title>
<link href="https://fonts.googleapis.com/css2?family=Montserrat:wght@400;500;600;700&display=swap" rel="stylesheet">
<style>
  :root {
    --backdrop: #8e8e8e;
    --card-white: #ffffff;
    --navy: #1b2a45;
    --text-grey: #4a4f57;
    --aqua: #5ecbdc;
    --sky: #36c2e9;
    --ocean: #3f6fb8;
    --icon-blue: #3a9fdc;
  }
  * { margin: 0; padding: 0; box-sizing: border-box; }
  html, body {
    width: 1200px;
    height: 588px;
    overflow: hidden;
  }
  body {
    background: var(--backdrop);
    font-family: "Montserrat", sans-serif;
    position: relative;
  }
  .card {
    position: absolute;
    width: 486px;
    height: 287px;
    border-radius: 24px;
    overflow: hidden;
  }
  .card-front {
    left: 87px;
    top: 141px;
    background: linear-gradient(90deg, var(--aqua) 0%, var(--sky) 35%, var(--ocean) 100%);
    display: flex;
    align-items: center;
    justify-content: center;
  }
  .brand {
    display: flex;
    align-items: center;
    gap: 12px;
  }
  .brand-dot {
    border-radius: 50%;
    flex: none;
  }
  .card-front .brand-dot {
    width: 40px;
    height: 40px;
    background: var(--card-white);
  }
  .card-front .brand-name {
    color: var(--card-white);
    font-weight: 600;
    font-size: 40px;
    letter-spacing: 0.5px;
  }
  .card-back {
    left: 622px;
    top: 143px;
    background: var(--card-white);
  }
  .card-back .brand {
    position: absolute;
    right: 22px;
    top: 27px;
    gap: 10px;
  }
  .card-back .brand-dot {
    width: 30px;
    height: 30px;
    background: var(--sky);
  }
  .card-back .brand-name {
    color: var(--navy);
    font-weight: 600;
    font-size: 31px;
    letter-spacing: 0.3px;
  }
  .holder {
    position: absolute;
    left: 24px;
    top: 153px;
  }
  .holder-name {
    color: var(--navy);
    font-weight: 700;
    font-size: 18.5px;
    letter-spacing: 0.3px;
  }
  .holder-title {
    color: var(--text-grey);
    font-weight: 400;
    font-size: 13px;
    margin-top: 3px;
  }
  .divider {
    position: absolute;
    left: 24px;
    right: 23px;
    top: 208px;
    height: 1px;
    background: var(--navy);
  }
  .contacts {
    position: absolute;
    left: 24px;
    top: 228px;
    list-style: none;
  }
  .contacts li {
    display: flex;
    align-items: center;
    gap: 6px;
    color: var(--text-grey);
    font-size: 13px;
    height: 19px;
  }
  .contacts svg { width: 11px; height: 11px; flex: none; }
  .website {
    position: absolute;
    right: 22px;
    top: 247px;
    color: var(--text-grey);
    font-size: 13px;
  }
  .website strong { color: var(--navy); font-weight: 600; }
  .accent-bar {
    position: absolute;
    left: 344px;
    width: 121px;
    bottom: 0;
    height: 10px;
    background: linear-gradient(90deg, var(--aqua), var(--ocean));
  }
</style>
</head>
<body>
  <section class="card card-front" aria-label="Card front">
    <div class="brand">
      <span class="brand-dot"></span>
      <span class="brand-name">VERODEX</span>
    </div>
  </section>

  <section class="card card-back" aria-label="Card back">
    <div class="brand">
      <span class="brand-dot"></span>
      <span class="brand-name">VERODEX</span>
    </div>

    <div class="holder">
      <h1 class="holder-name">MARCUS KELLER</h1>
      <p class="holder-title">President</p>
    </div>

    <div class="divider"></div>

    <ul class="contacts">
      <li>
        <svg viewBox="0 0 24 24" aria-hidden="true"><path fill="var(--icon-blue)" d="M6.6 10.8c1.4 2.8 3.8 5.1 6.6 6.6l2.2-2.2c.3-.3.7-.4 1-.2 1.1.4 2.3.6 3.6.6.6 0 1 .4 1 1V20c0 .6-.4 1-1 1C10.6 21 3 13.4 3 4c0-.6.4-1 1-1h3.5c.6 0 1 .4 1 1 0 1.3.2 2.5.6 3.6.1.3 0 .7-.2 1l-2.3 2.2z"/></svg>
        555-310-4821
      </li>
      <li>
        <svg viewBox="0 0 24 24" aria-hidden="true"><path fill="var(--icon-blue)" d="M2 5h20v14H2z"/><path fill="none" stroke="#fff" stroke-width="2" d="M2 6l10 7 10-7"/></svg>
        marcus@verodex.com
      </li>
    </ul>

    <p class="website">www.<strong>verodex</strong>.com</p>

    <div class="accent-bar"></div>
  </section>
</body>
</html>
```